Halvorsen Construction Needs a Business Card

Our current business card is very bland, and since we have a new logo, we would like a new business card design to reflect our company. It can be a single-sided or two-sided card, but it is important that our contact information appears on the same side. I am attaching a copy of our old card and our new logo. If you need the logo in another format than the one I'm sending, please let me know. This is the information that we must have on our card, but not necessarily in any specific order:
1) Our logo
2) General Contractor
3) Derek Halvorsen, Owner
4) 482 Commerce Ridge Road, Oakmont, Alabama 35971
5) Office: 256-384-7150
7) Fax: 256-384-7151
8) Cell: 256-619-7150
9) halvorsenconstruction@qrm.net
10) halvorsenconstruction.com (can be omitted if necessary)
Also, I will need files in a format that I can alter if any of the above information changes in the near future. Thank you in advance for your submissions!
Target Market(s)
Commercial and residential clients, architects, and subcontractors.
Industry/Entity Type
Business

```html
<!DOCTYPE html>
<html lang="en">
<head>
<meta charset="utf-8">
<title>Halvorsen Construction – Business Card</title>
<link rel="stylesheet" href="https://fonts.googleapis.com/css2?family=Crimson+Text:wght@400;700&display=swap">
<style>
  :root {
    --backdrop: #eec94f;
    --card: #5b5b59;
    --ink: #262626;
    --accent: #e9c02b;
    --mark: #1c1c1c;
  }
  * { margin: 0; padding: 0; box-sizing: border-box; }
  html, body {
    width: 1200px;
    height: 900px;
    overflow: hidden;
    background: var(--backdrop);
  }
  .business-card {
    position: absolute;
    left: 240px;
    top: 244px;
    width: 720px;
    height: 412px;
    background: var(--card);
    overflow: hidden;
    font-family: "Crimson Text", Georgia, serif;
    color: var(--ink);
  }
  .card-graphics {
    position: absolute;
    inset: 0;
  }
  .brand {
    position: absolute;
    left: 214px;
    top: 44px;
    display: flex;
    align-items: center;
    gap: 18px;
  }
  .brand-square {
    width: 78px;
    height: 78px;
    background: var(--ink);
    flex: none;
  }
  .brand-name {
    font-weight: 700;
    font-size: 38px;
    line-height: 1;
    letter-spacing: 0.06em;
    text-transform: uppercase;
    color: var(--ink);
  }
  .contact {
    position: absolute;
    left: 214px;
    top: 168px;
    font-size: 18px;
    line-height: 1.32;
    list-style: none;
  }
  .contact .person {
    font-weight: 700;
    font-size: 21px;
  }
</style>
</head>
<body>
  <section class="business-card" aria-label="Halvorsen Construction business card">
    <svg class="card-graphics" width="720" height="412" viewBox="0 0 720 412" aria-hidden="true">
      <g class="accent-stripes" fill="var(--accent)">
        <polygon points="150,0 164,0 92,170 78,170"/>
        <polygon points="174,0 188,0 116,170 102,170"/>
        <polygon points="198,0 212,0 140,170 126,170"/>
      </g>
      <g class="corner-bars" fill="var(--mark)">
        <rect x="36" y="300" width="8" height="62"/>
        <rect x="52" y="300" width="8" height="62"/>
        <rect x="68" y="300" width="8" height="62"/>
      </g>
    </svg>

    <div class="brand">
      <span class="brand-square" aria-hidden="true"></span>
      <span class="brand-name">Halvorsen Construction</span>
    </div>

    <ul class="contact">
      <li class="person">Derek Halvorsen</li>
      <li class="role">General Contractor</li>
      <li class="address">482 Commerce Ridge Road, Oakmont, Alabama 35971</li>
      <li class="phone">Office: 256-384-7150</li>
      <li class="fax">Fax: 256-384-7151</li>
      <li class="cell">Cell: 256-619-7150</li>
      <li class="email">halvorsenconstruction@qrm.net</li>
      <li class="web">www.halvorsenconstruction.com</li>
    </ul>
  </section>
</body>
</html>
```